Stationery Design Project

We need a stationery design for our Norwegian trucking company. We have existed for about 15 years and our 12 drivers uses relatively new vehicles to transport goods around in northern Norway. Long distance routes with fresh fish og food transport is our main operations.

We have already made alogo that's printed on our trucks. The logo and a picture of our trucks is attached. I think the logo i crappy, but since its already in use, changing it is not an option in this round. Still using a better colour scheme in the overall stationery and more interesting fonts is possible (altso in the logo).

Company details:
Name: Kjelvraket AS
Organisation nr 873 615 309
Post adress: 8642 Raudvik

I like minimalism and simplicity. I am avalibly for questions in normal GMT working hours either here or on mail: ivar@fjordlast.no

Reason: Hi. Im extending the deadline because I needed some time to find a vector file of our logo. Sorry for the inconvenience

Hi, and thanks for all your interest in the project. Some updates:

-          I have decided to commit to using one of the designs. Some designer will get the payment.

-          I have extended the deadline with 24 hours since I needed some time to find our firms vector logo (a slow Swedish man was holding me up)

-          We will not choose a design before the deadline. No need to rush.

-          We have received a lot of great design and think there is a need to specified the product we want to make:

o   Business Card for all our employers. I just need the design and will duplicate with the correct numbers and name myself. The information on should be: Logo, employer’s name, Phone number, email, website, Postal number and address. Use this as a template: logo, Leif Brattvoll, 47382066, Leif@fjordlast.no,, fjordlast.no, 8642 Raudvik. The order and placement of the information is your creative decision.

o   Stickers to put on the goods we travel. On the sticker the should be the following information: Logo, phone number, Tekst and link: Fraktæ av Kjelvraket. Ke du syns? Fjordlast.no/tilbakemelding (this means: Handled by Kjelvraket. What do you think Fjordlast.no/feedback -à the link will be a feedback form). The placement the information and size is your creative decision with some stings: we have been thinking of using Drukko for printing and see that a size about 6x6 cm, 8x5 or something like that. (with 3000 copies our budget is 200 punds). Any suggestions of other suppliers are welcome. Drukko price calculator http://www.drukkolabelhouse.co.uk/digital-litho-printing/printing-labels-tags/stickers/

o   Letterhead with logo, address, phone number and organizational number.

o   Envelopes with logo,address, phone number and organizational number.

Have a nice day.

 

 

• Using the blue colour in the logo and using a similar graphic approch.

```html
<!DOCTYPE html>
<html lang="no">
<head>
<meta charset="utf-8">
<title>Kjelvraket – visittkort</title>
<link rel="stylesheet" href="https://fonts.googleapis.com/css2?family=Source+Sans+3:wght@400;600;700;800&display=swap">
<style>
  :root {
    --backdrop: #b9bcc0;
    --paper: #ffffff;
    --navy: #0b4d9e;
    --azure: #0a74bc;
    --brand: #0f5aa8;
    --ink: #2a2a2a;
    --edge: #7d7d7d;
  }
  * { box-sizing: border-box; margin: 0; padding: 0; }
  html, body { width: 1200px; height: 751px; overflow: hidden; }
  body {
    background: var(--backdrop);
    font-family: "Source Sans 3", sans-serif;
    position: relative;
  }
  .card {
    position: absolute;
    width: 525px;
    height: 300px;
    border-radius: 24px;
    overflow: hidden;
  }
  .card--front { left: 50px; top: 50px; background: var(--paper); }
  .card--white { left: 620px; top: 50px; background: var(--paper); border: 1px solid var(--edge); }
  .card--navy  { left: 50px; top: 388px; background: var(--navy); }
  .card--azure { left: 620px; top: 388px; background: var(--azure); }

  .brand {
    position: absolute;
    left: 0; right: 0;
    display: flex;
    justify-content: center;
    align-items: center;
    gap: 14px;
    font-weight: 800;
    font-size: 46px;
    letter-spacing: 0.5px;
    color: var(--brand);
  }
  .brand__dot {
    width: 22px; height: 22px; border-radius: 50%;
    background: currentColor;
  }
  .card--front .brand { top: 62px; }
  .card--white .brand, .card--navy .brand, .card--azure .brand { top: 112px; }
  .card--navy .brand, .card--azure .brand { color: var(--paper); }

  .holder {
    position: absolute;
    top: 164px; left: 0; right: 0;
    text-align: center;
    font-weight: 700;
    font-size: 19px;
    color: var(--navy);
  }
  .band { position: absolute; left: 0; top: 0; width: 525px; height: 300px; }
  .contact {
    position: absolute;
    left: 0; right: 0;
    display: flex;
    justify-content: center;
    align-items: center;
    gap: 12px;
    color: var(--paper);
    font-size: 15px;
  }
  .contact--first { top: 233px; }
  .contact--second { top: 258px; }
  .contact span { display: inline-flex; align-items: center; gap: 5px; }
  .contact svg { width: 11px; height: 11px; fill: var(--paper); }

  .web {
    position: absolute;
    left: 0; right: 0;
    top: 250px;
    text-align: center;
    font-size: 17px;
    letter-spacing: 3.6px;
    color: var(--paper);
  }
  .card--white .web { color: var(--ink); }
</style>
</head>
<body>

  <section class="card card--front" aria-label="Visittkort forside">
    <div class="brand"><span class="brand__dot"></span>Kjelvraket</div>
    <p class="holder">Leif Brattvoll</p>
    <svg class="band" viewBox="0 0 525 300" aria-hidden="true">
      <path d="M0 238 Q262 160 525 238" fill="none" stroke="var(--navy)" stroke-width="2"/>
      <path d="M0 252 Q262 172 525 252 L525 300 L0 300 Z" fill="var(--navy)"/>
    </svg>
    <div class="contact contact--first">
      <span><svg viewBox="0 0 12 12"><path d="M2 1h3l1 3-2 1a6 6 0 0 0 3 3l1-2 3 1v3c0 .5-.5 1-1 1A10 10 0 0 1 1 2c0-.5.5-1 1-1z"/></svg>47382066</span>
      <span>Org nr 873 615 309</span>
    </div>
    <div class="contact contact--second">
      <span><svg viewBox="0 0 12 12"><path d="M0 3h12v7H0z M0 3l6 4 6-4" /></svg>Leif@fjordlast.no</span>
      <span><svg viewBox="0 0 12 12"><circle cx="6" cy="6" r="6"/></svg>www.fjordlast.no</span>
      <span><svg viewBox="0 0 12 12"><path d="M1 12V5l5-4 5 4v7z"/></svg>8642 Raudvik</span>
    </div>
  </section>

  <section class="card card--white" aria-label="Visittkort bakside hvit">
    <div class="brand"><span class="brand__dot"></span>Kjelvraket</div>
    <p class="web">www.fjordlast.no</p>
  </section>

  <section class="card card--navy" aria-label="Visittkort bakside mørkeblå">
    <div class="brand"><span class="brand__dot"></span>Kjelvraket</div>
    <p class="web">www.fjordlast.no</p>
  </section>

  <section class="card card--azure" aria-label="Visittkort bakside blå">
    <div class="brand"><span class="brand__dot"></span>Kjelvraket</div>
    <p class="web">www.fjordlast.no</p>
  </section>

</body>
</html>
```